Foot doctor needs feet friendly business cards.

Business cards for Podiatrist. Needs to look professional and modern. Back side put an appointment card, and try to put a little basic street map somewhere on card along with all of our contact info below:

Marcus Dovan, DPM, Inc.
Diplomate, National Council of Lower Limb Medicine
Call: 1.877.Toes.482
1.555.283.9146
Fax: 1.555.671.3820
Email: info@DrDovanclinic.example
Web: www.DrDovanclinic.example
2847 W. Harbor Ln. Suite 204
Costa Mesa, CA 90000

```html
<!DOCTYPE html>
<html lang="en">
<head>
<meta charset="utf-8">
<title>Marcus Dovan, DPM, Inc. — Business Card</title>
<link rel="stylesheet" href="https://fonts.googleapis.com/css2?family=Open+Sans:ital,wght@0,400;0,600;0,700;1,400;1,600&display=swap">
<style>
  :root {
    --stage: #3b3432;
    --card: #ffffff;
    --brand-blue: #2e5a8a;
    --ink: #2a2a2a;
    --rule: #222222;
    --skin-light: #f0c9a4;
    --skin-mid: #d9a07a;
    --sheet: #f4f2ef;
  }
  * { margin: 0; padding: 0; box-sizing: border-box; }
  html, body { width: 1200px; height: 844px; overflow: hidden; }
  body {
    background: var(--stage);
    font-family: "Open Sans", Arial, sans-serif;
    position: relative;
  }
  .card {
    position: absolute;
    width: 520px;
    height: 297px;
    background: var(--card);
    overflow: hidden;
    box-shadow: 0 8px 24px rgba(0,0,0,.35);
  }
  /* Front */
  .card-front { left: 50px; top: 273px; }
  .band { position: absolute; left: 0; width: 100%; background: var(--brand-blue); }
  .band-top { top: 0; height: 11px; }
  .band-bottom { bottom: 0; height: 14px; }
  .feet-photo {
    position: absolute;
    left: 80px; right: 0; bottom: 14px; height: 160px;
    background:
      radial-gradient(ellipse 60% 70% at 70% 85%, var(--skin-mid), transparent 70%),
      radial-gradient(ellipse 70% 60% at 30% 95%, var(--skin-light), transparent 70%),
      linear-gradient(180deg, #ffffff 0%, var(--sheet) 45%, #e9dcd0 100%);
  }
  .identity { position: absolute; left: 26px; top: 52px; color: var(--ink); }
  .name {
    color: var(--brand-blue);
    font-weight: 600;
    font-size: 21px;
    text-transform: uppercase;
    letter-spacing: .3px;
    line-height: 1.1;
  }
  .name small { font-size: 17px; }
  .credential { font-size: 14.5px; line-height: 1.25; margin-top: 2px; }
  .address { font-size: 14.5px; line-height: 1.3; margin-top: 16px; }
  .contact {
    position: absolute; right: 22px; top: 24px;
    list-style: none; text-align: right;
    font-size: 13px; line-height: 1.42; color: var(--ink);
  }
  .contact li { display: flex; justify-content: flex-end; align-items: center; gap: 7px; }
  .contact svg { width: 11px; height: 11px; fill: var(--brand-blue); flex: none; }

  /* Back */
  .card-back { left: 630px; top: 273px; }
  .tab { position: absolute; width: 24px; height: 44px; background: var(--brand-blue); }
  .tab-right { right: 0; top: 20px; }
  .tab-left { left: 0; top: 150px; }
  .appt-title {
    position: absolute; top: 30px; width: 100%; text-align: center;
    color: var(--brand-blue); font-weight: 600; font-size: 13px; letter-spacing: .5px;
  }
  .appt-form { position: absolute; left: 44px; right: 44px; top: 60px; }
  .field {
    display: flex; align-items: flex-end; gap: 6px;
    height: 30px; font-size: 12.5px; color: var(--ink);
  }
  .field .line { flex: 1; border-bottom: 1px solid var(--rule); height: 1px; }
  .field .label { white-space: nowrap; }
  .note {
    position: absolute; left: 40px; right: 40px; top: 205px;
    text-align: center; font-style: italic; font-size: 13px; line-height: 1.4;
    color: var(--brand-blue);
  }
</style>
</head>
<body>

<section class="card card-front" aria-label="Business card front">
  <div class="band band-top"></div>
  <div class="feet-photo" role="img" aria-label="Photo of a family's bare feet peeking out from under white bed sheets"></div>
  <div class="identity">
    <h1 class="name">Marcus Dovan, <small>DPM, Inc.</small></h1>
    <p class="credential">Diplomate, National Council of<br>Lower Limb Medicine</p>
    <p class="address">2847 W. Harbor Ln. Suite 204<br>Costa Mesa, CA 90000</p>
  </div>
  <ul class="contact">
    <li>1.877.Toes.482 <svg viewBox="0 0 12 12"><path d="M1 3c0-1 1-2 2-2l1.5 2.5-1 1c.6 1.3 1.7 2.4 3 3l1-1L10 8c0 1-1 2-2 2C4 10 1 7 1 3z"/></svg></li>
    <li>1.555.283.9146 <svg viewBox="0 0 12 12"><path d="M1 4h10v6H1zM3 1h6v3H3z"/></svg></li>
    <li>1.555.671.3820 <svg viewBox="0 0 12 12"><path d="M1 2h10v8H1zM1 2l5 4 5-4" stroke="#fff" stroke-width="1"/></svg></li>
    <li>info@DrDovanclinic.example <svg viewBox="0 0 12 12"><path d="M1 3h10v7H1z"/><path d="M1 3l5 4 5-4" fill="none" stroke="#fff" stroke-width="1"/></svg></li>
    <li>www.DrDovanclinic.example <svg viewBox="0 0 12 12"><path d="M3 9l6-6M2 7l-1 1a2 2 0 003 3l1-1M10 5l1-1a2 2 0 00-3-3L7 2" fill="none" stroke="#2e5a8a" stroke-width="1.4"/></svg></li>
  </ul>
  <div class="band band-bottom"></div>
</section>

<section class="card card-back" aria-label="Appointment card back">
  <div class="tab tab-right"></div>
  <div class="tab tab-left"></div>
  <h2 class="appt-title">APPOINTMENT</h2>
  <div class="appt-form">
    <div class="field"><span class="label">For :</span><span class="line"></span><span class="label">Time :</span><span class="line"></span></div>
    <div class="field"><span class="label">Date :</span><span class="line"></span></div>
    <div class="field"><span class="label">Location :</span><span class="line"></span></div>
    <div class="field"><span class="line"></span></div>
  </div>
  <p class="note">If you are unable to keep appointment, please contact<br>us as soon as possible. Call 877 555 0142</p>
</section>

</body>
</html>
```